Home Remodeling company needs a business card design

we need a business card design for home remodeling company in hamilton county, indiana USA. we offers a wide range of construction services including whole house renovations, Design and Build Basements and Kitchen and Bathroom Remodeling . we would like to see designs for both site of business card that use the same color of the company logo and also including all information below :
1- Karim Feltous CEO / General Contractor
2- all company contacts Telephone numbers ( 1-888-DULOM-47 ) ( 317-555-0193) email address ( info@dulomhome.com) website ( www.dulomhome.com ) and social media logos (Facebook- twitter- google plus )
3- company logo
4- licensed . insured . bonded

```html
<!DOCTYPE html>
<html lang="en">
<head>
<meta charset="utf-8">
<title>Dulom Home Remodeling – Business Card</title>
<link href="https://fonts.googleapis.com/css2?family=Source+Sans+3:wght@400;600&display=swap" rel="stylesheet">
<style>
  :root {
    --backdrop: #2c2e33;
    --card: #ffffff;
    --ink: #2b2b2b;
    --brand-red: #d0202a;
    --brand-grey: #3a3a3c;
  }
  * { box-sizing: border-box; margin: 0; padding: 0; }
  html, body {
    width: 1200px; height: 864px; overflow: hidden;
    background: var(--backdrop);
    font-family: "Source Sans 3", "Segoe UI", sans-serif;
    color: var(--ink);
  }
  .sheet {
    position: relative; width: 1200px; height: 864px;
    display: flex; flex-direction: column; align-items: center;
    justify-content: center; gap: 44px;
  }
  .card {
    position: relative; width: 560px; height: 320px;
    background: var(--card);
    box-shadow: 0 8px 24px rgba(0,0,0,.35);
  }

  /* company name */
  .brand { display: flex; align-items: center; gap: 10px; }
  .brand-square { width: 12px; height: 12px; background: var(--brand-red); flex: none; }
  .brand-name {
    font-weight: 600; font-size: 30px; line-height: 1.1;
    color: var(--brand-grey);
  }

  /* front */
  .card-front { display: flex; flex-direction: column; align-items: center; justify-content: center; }
  .front-tagline {
    margin-top: 16px; display: flex; align-items: center; gap: 10px;
    font-size: 17px; font-weight: 600; color: var(--ink);
  }
  .dot { width: 7px; height: 7px; border-radius: 50%; background: var(--brand-red); }

  /* back */
  .card-back { padding: 34px 36px; }
  .card-back .brand-name { font-size: 28px; }
  .person-name { margin-top: 22px; font-size: 19px; font-weight: 600; color: var(--brand-red); }
  .person-title { font-size: 15px; color: var(--ink); }
  .contact-list { list-style: none; margin-top: 14px; }
  .contact-item { display: flex; align-items: center; gap: 8px; font-size: 15px; line-height: 21px; }
  .contact-icon { width: 12px; height: 12px; flex: none; }
  .social-list { display: flex; gap: 8px; margin-top: 12px; }
  .social-dot { width: 17px; height: 17px; border-radius: 50%; background: var(--ink); }
</style>
</head>
<body>
<main class="sheet">

  <section class="card card-front" aria-label="Card front">
    <div class="brand">
      <span class="brand-square"></span>
      <span class="brand-name">Dulom Home Remodeling</span>
    </div>
    <p class="front-tagline">
      Licensed <span class="dot"></span> Insured <span class="dot"></span> Bonded
    </p>
  </section>

  <section class="card card-back" aria-label="Card back">
    <div class="brand">
      <span class="brand-square"></span>
      <span class="brand-name">Dulom Home Remodeling</span>
    </div>

    <p class="person-name">Karim Feltous</p>
    <p class="person-title">CEO / General Contractor</p>

    <ul class="contact-list">
      <li class="contact-item">
        <svg class="contact-icon" viewBox="0 0 24 24"><path fill="#d0202a" d="M6.6 10.8a15.1 15.1 0 0 0 6.6 6.6l2.2-2.2c.3-.3.7-.4 1-.2 1.1.4 2.3.6 3.6.6.6 0 1 .4 1 1V20c0 .6-.4 1-1 1C10.6 21 3 13.4 3 4c0-.6.4-1 1-1h3.5c.6 0 1 .4 1 1 0 1.3.2 2.5.6 3.6.1.3 0 .7-.2 1z"/></svg>
        1-888-DULOM-47
      </li>
      <li class="contact-item">
        <svg class="contact-icon" viewBox="0 0 24 24"><path fill="#d0202a" d="M6.6 10.8a15.1 15.1 0 0 0 6.6 6.6l2.2-2.2c.3-.3.7-.4 1-.2 1.1.4 2.3.6 3.6.6.6 0 1 .4 1 1V20c0 .6-.4 1-1 1C10.6 21 3 13.4 3 4c0-.6.4-1 1-1h3.5c.6 0 1 .4 1 1 0 1.3.2 2.5.6 3.6.1.3 0 .7-.2 1z"/></svg>
        317-555-0193
      </li>
      <li class="contact-item">
        <svg class="contact-icon" viewBox="0 0 24 24"><rect x="2" y="5" width="20" height="14" fill="#d0202a"/><path d="M2 5l10 8 10-8" fill="none" stroke="#fff" stroke-width="2"/></svg>
        info@dulomhome.com
      </li>
      <li class="contact-item">
        <svg class="contact-icon" viewBox="0 0 24 24"><g fill="none" stroke="#4a4a4a" stroke-width="2.4" stroke-linecap="round"><path d="M10 14a4 4 0 0 0 5.7 0l3.5-3.5a4 4 0 0 0-5.7-5.7L12 6.3"/><path d="M14 10a4 4 0 0 0-5.7 0l-3.5 3.5a4 4 0 0 0 5.7 5.7l1.5-1.5"/></g></svg>
        www.dulomhome.com
      </li>
    </ul>

    <div class="social-list" aria-label="Social media">
      <span class="social-dot"></span>
      <span class="social-dot"></span>
      <span class="social-dot"></span>
    </div>
  </section>

</main>
</body>
</html>
```